Zolvana Stationary and Branding Documents

Corporate Identity Branding stationary needed for IT Recruiting Firm.

I already have a Logo, business cards and website. I need to get designs completed for the remaining corporate identity documents.

The documentation should use similar colors as my website and business card. The designs should modern and clean.

http://zolvanaworks.example/

Target Market(s)

Information Technology Industry

Industry/Entity Type

Information Technology

Colors
3377b5
0255a3
fbee3e
f78f20
f37122
33a6d7
000000
0592cd

Requirements
Must have
• Letter Head
• Folder Design
• PowerPoint Design
• Invoice
• Envelope
Nice to have
• Proposal
• Flyer
• Brochure
Should not have
• Logo
• Business Cards
• Website

```html
<!DOCTYPE html>
<html lang="en">
<head>
<meta charset="utf-8">
<title>Zolvana Folder Design</title>
<link rel="stylesheet" href="https://fonts.googleapis.com/css2?family=Open+Sans:wght@400;600&family=Cinzel:wght@500&display=swap">
<style>
  :root {
    --page-bg: #1a74b4;
    --folder-blue: #1f7cc4;
    --folder-blue-deep: #0255a3;
    --accent-orange: #f37122;
    --accent-orange-light: #f78f20;
    --navy: #23406f;
    --sky: #33a6d7;
    --white: #ffffff;
    --photo-light: #cfe9f5;
    --photo-mid: #8fc3df;
  }
  html, body {
    margin: 0;
    width: 1200px;
    height: 847px;
    overflow: hidden;
    background: var(--page-bg);
    font-family: "Open Sans", sans-serif;
  }
  .canvas {
    position: relative;
    width: 1200px;
    height: 847px;
    display: flex;
    justify-content: center;
    align-items: center;
    gap: 0;
  }
  .folder-panel {
    width: 520px;
    height: 700px;
    display: block;
    box-shadow: 0 10px 30px rgba(0, 0, 0, 0.25);
  }
  .brand-name { font-family: "Open Sans", sans-serif; font-weight: 400; fill: var(--white); }
  .brand-tagline { font-family: "Open Sans", sans-serif; font-weight: 400; fill: var(--accent-orange-light); letter-spacing: 2px; }
  .contact-line { font-family: "Open Sans", sans-serif; font-size: 8.5px; fill: var(--white); }
  .band-copy { font-family: "Open Sans", sans-serif; font-size: 7.6px; fill: var(--white); letter-spacing: 0.2px; }
  .band-slogan { font-family: "Cinzel", serif; font-size: 17px; fill: var(--white); letter-spacing: 1px; }
  .site-address { font-family: "Open Sans", sans-serif; font-weight: 600; font-size: 10px; fill: var(--white); }
</style>
</head>
<body>
<main class="canvas">

  <!-- Back cover -->
  <svg class="folder-panel back-cover" viewBox="0 0 520 700" xmlns="http://www.w3.org/2000/svg">
    <defs>
      <linearGradient id="photoTone" x1="0" y1="0" x2="1" y2="1">
        <stop offset="0" stop-color="#e9f4fa"/>
        <stop offset="1" stop-color="#7fb2d3"/>
      </linearGradient>
    </defs>
    <rect width="520" height="700" fill="var(--folder-blue)"/>

    <g class="photo-tile" role="img" aria-label="Photo of a businesswoman on the phone at her desk" transform="translate(95 140) rotate(-30)">
      <rect x="-52" y="-52" width="104" height="104" rx="16" fill="var(--white)"/>
      <rect x="-46" y="-46" width="92" height="92" rx="12" fill="url(#photoTone)"/>
    </g>
    <g class="photo-tile" role="img" aria-label="Photo of colleagues in a meeting room" transform="translate(240 110) rotate(-30)">
      <rect x="-52" y="-52" width="104" height="104" rx="16" fill="var(--white)"/>
      <rect x="-46" y="-46" width="92" height="92" rx="12" fill="url(#photoTone)"/>
    </g>
    <g class="photo-tile" role="img" aria-label="Photo of business people shaking hands" transform="translate(390 70) rotate(-30)">
      <rect x="-52" y="-52" width="104" height="104" rx="16" fill="var(--white)"/>
      <rect x="-46" y="-46" width="92" height="92" rx="12" fill="url(#photoTone)"/>
    </g>

    <g class="swoosh">
      <path d="M0 308 Q300 330 520 170 L520 200 Q300 360 0 340 Z" fill="var(--navy)"/>
      <path d="M0 300 Q300 322 520 163 L520 172 Q300 332 0 310 Z" fill="var(--white)"/>
      <path d="M0 284 Q300 304 520 148 L520 163 Q300 320 0 300 Z" fill="var(--accent-orange)"/>
      <path d="M0 279 Q300 298 520 144 L520 148 Q300 304 0 284 Z" fill="var(--white)"/>
    </g>

    <g class="brand-block">
      <text class="brand-name" x="40" y="590" font-size="44">zolvana</text>
      <text class="brand-tagline" x="48" y="606" font-size="9">BUSINESS SOLUTION LLC</text>
      <text class="contact-line" x="40" y="626">● Two Harbor Plaza 410 Linden Avenue  ● 5550142871</text>
      <text class="contact-line" x="40" y="639">● info@zolvanaworks.example  ● zolvanaworks.example</text>
    </g>

    <rect class="copy-band" x="0" y="650" width="520" height="28" fill="var(--accent-orange)"/>
    <text class="band-copy" x="10" y="661">ELITE IT TALENT IS NO ACCIDENT. IT TAKES PERSONAL DRIVE AND SMARTS, PLUS SMART CAREER COUNSELING. DO YOU HAVE WHAT IT</text>
    <text class="band-copy" x="10" y="672">TAKES? IF YOU DO, WE PROVIDE MENTORING AND COUNSEL, AND WE'LL STAY WITH YOU THROUGHOUT YOUR CAREER.</text>
    <rect class="edge-line" x="0" y="688" width="520" height="3" fill="var(--white)"/>
  </svg>

  <!-- Front cover -->
  <svg class="folder-panel front-cover" viewBox="0 0 520 700" xmlns="http://www.w3.org/2000/svg">
    <defs>
      <linearGradient id="heroTone" x1="0" y1="0" x2="1" y2="0">
        <stop offset="0" stop-color="var(--photo-mid)"/>
        <stop offset="0.5" stop-color="var(--photo-light)"/>
        <stop offset="1" stop-color="#f4f9fc"/>
      </linearGradient>
    </defs>
    <rect width="520" height="700" fill="var(--folder-blue)"/>

    <path class="hero-photo" role="img" aria-label="Photo of three smiling colleagues in a bright glass office"
          d="M0 0 H520 V142 Q260 120 0 170 Z" fill="url(#heroTone)"/>
    <path d="M0 170 Q260 120 520 142 L520 160 Q260 136 0 186 Z" fill="var(--accent-orange)"/>
    <path d="M0 186 Q260 136 520 160 L520 168 Q260 144 0 193 Z" fill="var(--white)"/>

    <g class="brand-block">
      <text class="brand-name" x="50" y="262" font-size="58">zolvana</text>
      <text class="brand-tagline" x="62" y="284" font-size="11">BUSINESS SOLUTION LLC</text>
    </g>

    <rect class="slogan-band" x="0" y="560" width="520" height="28" fill="var(--accent-orange)"/>
    <text class="band-slogan" x="330" y="580" text-anchor="middle">JOIN THE ELITE</text>

    <rect class="edge-line" x="0" y="628" width="520" height="3" fill="var(--white)"/>
    <rect class="site-pill" x="290" y="618" width="150" height="22" rx="6" fill="var(--navy)"/>
    <text class="site-address" x="365" y="633" text-anchor="middle">zolvanaworks.example</text>
  </svg>

</main>
</body>
</html>
```